Sea Shipping Logistics Company

The business is a logistics company (sea shipping and other special logistics) and also sales of bulk building materials.
The Design should be minimalistic and give a feeling of power and connectivity.
When the client sees the card, they should get a feeling of confident. Dark overall color (background) and print should be red / white .See logo. The card will be printed on trifecta with the middle color being red.

One side should be the logo and a 5 / 6 word slogan
And other side name, contact (phone/email) and a QR Code.

Target Market(s)

Construction companies / Oil & Gas related companies

Industry/Entity Type

Sea Bulk Shipping Logistics

Contact Information for Business Card

Name, Telephone number, Email address, Website URL, QR Code (see description)

Font styles to use
Sans Serif

Requirements
Must have
• No idea
Nice to have
• Minimalistic, but strong and powerful look and feel.

```html
<!DOCTYPE html>
<html lang="en">
<head>
<meta charset="utf-8">
<title>Korven Business Card</title>
<link rel="stylesheet" href="https://fonts.googleapis.com/css2?family=Archivo:wght@400;600;800&display=swap">
<style>
  :root {
    --stage: #2a2a2c;
    --card: #1c1d20;
    --red: #ea3a31;
    --white: #ffffff;
    --muted: #e6e6e6;
    --rule: #8a8a8a;
  }
  * { box-sizing: border-box; margin: 0; padding: 0; }
  html, body {
    width: 1200px; height: 1015px; overflow: hidden;
    background: var(--stage);
    font-family: "Archivo", Arial, sans-serif;
  }
  .card {
    position: absolute; left: 220px;
    width: 760px; height: 420px;
    background: var(--card);
    overflow: hidden;
  }
  .card--front { top: 70px; }
  .card--back { top: 530px; }

  .brand { position: absolute; display: flex; align-items: center; gap: 22px; }
  .brand__square { border: 3px solid var(--white); }
  .brand__name {
    color: var(--white); font-weight: 800; letter-spacing: 2px; line-height: 1;
  }

  .card--front .brand { left: 190px; top: 95px; }
  .card--front .brand__square { width: 110px; height: 110px; }
  .card--front .brand__name { font-size: 82px; }

  .front-band {
    position: absolute; left: 0; right: 0; top: 262px; height: 62px;
    background: var(--red);
    display: flex; align-items: center; justify-content: center;
  }
  .front-band__url {
    color: var(--white); font-size: 24px; font-weight: 400; letter-spacing: 1px;
  }

  .card--back .brand { left: 60px; top: 180px; }
  .card--back .brand__square { width: 78px; height: 78px; }
  .card--back .brand__name { font-size: 54px; color: var(--muted); }

  .divider {
    position: absolute; left: 418px; top: 80px; width: 1px; height: 230px;
    background: var(--rule);
  }

  .contact { position: absolute; left: 450px; top: 92px; }
  .contact__name {
    color: var(--red); font-weight: 800; font-size: 26px; letter-spacing: 0.5px;
    text-transform: uppercase;
  }
  .contact__role { color: var(--white); font-size: 19px; margin-top: 2px; }
  .contact__list { list-style: none; margin-top: 22px; }
  .contact__item {
    display: flex; align-items: center; gap: 10px;
    color: var(--white); font-size: 18px; margin-bottom: 10px;
  }
  .contact__icon { width: 28px; height: 28px; flex: none; }
  .accent { color: var(--red); }

  .back-band { position: absolute; left: 0; right: 0; bottom: 0; height: 26px; display: flex; }
  .back-band__red { width: 62%; background: var(--red); }
  .back-band__gap { width: 6px; background: var(--card); }
  .back-band__white { flex: 1; background: var(--white); margin-top: -18px; }
</style>
</head>
<body>

<section class="card card--front">
  <div class="brand">
    <span class="brand__square"></span>
    <span class="brand__name">KORVEN</span>
  </div>
  <div class="front-band">
    <span class="front-band__url">www.korvenline.com</span>
  </div>
</section>

<section class="card card--back">
  <div class="brand">
    <span class="brand__square"></span>
    <span class="brand__name">KORVEN</span>
  </div>

  <span class="divider"></span>

  <div class="contact">
    <p class="contact__name">Daniel Marsh</p>
    <p class="contact__role">Managing Director</p>
    <ul class="contact__list">
      <li class="contact__item">
        <svg class="contact__icon" viewBox="0 0 28 28" aria-hidden="true">
          <rect x="1" y="1" width="26" height="26" fill="none" stroke="#ea3a31" stroke-width="1.5"/>
          <path d="M9 8c1-1 2-1 3 0l1 2c0 1-1 1-1 2 1 2 2 3 4 4 1 0 1-1 2-1l2 1c1 1 1 2 0 3-2 2-5 1-8-2s-4-6-3-9z" fill="#ea3a31"/>
        </svg>
        044-555 010 200
      </li>
      <li class="contact__item">
        <svg class="contact__icon" viewBox="0 0 28 28" aria-hidden="true">
          <rect x="1" y="1" width="26" height="26" fill="none" stroke="#ea3a31" stroke-width="1.5"/>
          <rect x="6" y="9" width="16" height="11" fill="#ea3a31"/>
          <path d="M6 9l8 6 8-6" fill="none" stroke="#1c1d20" stroke-width="1.5"/>
        </svg>
        info@korvenline.com
      </li>
      <li class="contact__item">
        <svg class="contact__icon" viewBox="0 0 28 28" aria-hidden="true">
          <rect x="1" y="1" width="26" height="26" fill="none" stroke="#ea3a31" stroke-width="1.5"/>
          <g fill="none" stroke="#ea3a31" stroke-width="1.4">
            <circle cx="14" cy="14" r="8"/>
            <ellipse cx="14" cy="14" rx="3.5" ry="8"/>
            <path d="M6 14h16M7.5 10h13M7.5 18h13"/>
          </g>
        </svg>
        <span>www.<span class="accent">korvenline</span>.com</span>
      </li>
    </ul>
  </div>

  <div class="back-band">
    <span class="back-band__red"></span>
    <span class="back-band__gap"></span>
    <span class="back-band__white"></span>
  </div>
</section>

</body>
</html>
```